Business Card Design

Looking for business card designs for a new business. there will be two cards of the same design (both lots of information below in contact info). We would like the logo diagonally across the card with the information split above and below the logo similar to sketch. happy to look at similar alternatives
Please use same colours as in logo design

Industry/Entity Type

Business

Contact Information for Business Card

Dwight Halloran
mob - 0491 738 204
ph - 02 6148 3920
fax - 02 6148 3975
email - dwight@kestrelbeams.com.au
14 Larkmoor Road, Taminda NSW 2340

Colin Marchetti
mob - 0438 912 557
ph - 02 6148 3920
fax - 02 6148 3975
email - colin@kestrelbeams.com.au

```html
<!DOCTYPE html>
<html lang="en">
<head>
<meta charset="utf-8">
<title>Kestrel Beams – Business Cards</title>
<link href="https://fonts.googleapis.com/css2?family=Open+Sans:wght@400;600;700&display=swap" rel="stylesheet">
<style>
  :root {
    --teal: #0d7b76;
    --ink: #111111;
    --paper: #ffffff;
    --backdrop: #e9e6e1;
    --text-dark: #2b2b2b;
  }
  * { box-sizing: border-box; margin: 0; padding: 0; }
  html, body {
    width: 1145px; height: 1200px; overflow: hidden;
    background: var(--backdrop);
    font-family: "Open Sans", sans-serif;
  }
  .stage { position: relative; width: 1145px; height: 1200px; }
  .card {
    position: absolute; width: 945px; height: 537px;
    background: var(--paper);
    border: 1px solid #444;
    overflow: hidden;
  }
  .card--front { left: 164px; top: 46px; }
  .card--back { left: 44px; top: 625px; }

  .wordmark {
    position: absolute; left: 0; right: 0;
    display: flex; justify-content: center; align-items: center; gap: 16px;
  }
  .wordmark__square { width: 46px; height: 46px; background: var(--teal); }
  .wordmark__name {
    font-weight: 700; font-size: 66px; color: var(--ink);
    letter-spacing: -0.5px; line-height: 1;
  }
  .card--front .wordmark { top: 96px; }
  .card--back .wordmark { top: 216px; }

  .holder-name {
    position: absolute; top: 298px; left: 0; right: 0;
    text-align: center; color: var(--teal);
    font-weight: 700; font-size: 29px;
  }
  .rule {
    position: absolute; top: 370px; left: 0; right: 0;
    height: 5px; background: var(--ink);
  }
  .contact-band {
    position: absolute; top: 381px; left: 0; right: 0; bottom: 0;
    background: var(--teal); color: var(--paper);
  }
  .contact-col { position: absolute; top: 26px; display: flex; flex-direction: column; gap: 10px; }
  .contact-col--office { right: 550px; align-items: flex-end; font-size: 22px; }
  .contact-col--direct { left: 430px; align-items: flex-start; font-size: 22px; }
  .contact-divider {
    position: absolute; left: 413px; top: 20px; width: 1px; height: 118px;
    background: rgba(255,255,255,0.7);
  }
  .contact-line { display: flex; align-items: center; gap: 6px; height: 30px; line-height: 1; white-space: nowrap; }
  .contact-line--email { font-size: 19px; }
  .contact-line svg { width: 19px; height: 19px; fill: var(--paper); flex: none; }

  .web-address {
    position: absolute; top: 424px; left: 0; right: 0;
    text-align: center; font-size: 28px; letter-spacing: 3px; color: var(--text-dark);
  }
  .web-address strong { font-weight: 700; }
</style>
</head>
<body>
<main class="stage">
  <section class="card card--front">
    <div class="wordmark">
      <span class="wordmark__square"></span>
      <span class="wordmark__name">Kestrel Beams</span>
    </div>
    <p class="holder-name">Colin Marchetti</p>
    <div class="rule"></div>
    <div class="contact-band">
      <div class="contact-col contact-col--office">
        <div class="contact-line">
          <svg viewBox="0 0 24 24" aria-hidden="true"><path d="M6.6 10.8a15 15 0 0 0 6.6 6.6l2.2-2.2c.3-.3.7-.4 1-.2 1.1.4 2.3.6 3.6.6.6 0 1 .4 1 1V20c0 .6-.4 1-1 1C10.6 21 3 13.4 3 4c0-.6.4-1 1-1h3.5c.6 0 1 .4 1 1 0 1.3.2 2.5.6 3.6.1.3 0 .7-.2 1z"/></svg>
          <span>02 6148 3920</span>
        </div>
        <div class="contact-line"><span>14 Larkmoor Road</span></div>
        <div class="contact-line"><span>Calloway NSW 2351</span></div>
      </div>
      <div class="contact-divider"></div>
      <div class="contact-col contact-col--direct">
        <div class="contact-line">
          <svg viewBox="0 0 24 24" aria-hidden="true"><path d="M8 1h8a2 2 0 0 1 2 2v18a2 2 0 0 1-2 2H8a2 2 0 0 1-2-2V3a2 2 0 0 1 2-2zm0 3v13h8V4zm4 15a1 1 0 1 0 0 2 1 1 0 0 0 0-2z"/></svg>
          <span>0438 912 557</span>
        </div>
        <div class="contact-line">
          <svg viewBox="0 0 24 24" aria-hidden="true"><path d="M7 2h8l3 3v4H7zM4 10h16a2 2 0 0 1 2 2v7a2 2 0 0 1-2 2H4a2 2 0 0 1-2-2v-7a2 2 0 0 1 2-2zm3 3v2h10v-2z"/></svg>
          <span>02 6148 3975</span>
        </div>
        <div class="contact-line contact-line--email">
          <svg viewBox="0 0 24 24" aria-hidden="true"><path d="M3 5h18a1 1 0 0 1 1 1v12a1 1 0 0 1-1 1H3a1 1 0 0 1-1-1V6a1 1 0 0 1 1-1zm1 2.5V8l8 5 8-5v-.5z"/></svg>
          <span>colin@kestrelbeams.com.au</span>
        </div>
      </div>
    </div>
  </section>

  <section class="card card--back">
    <div class="wordmark">
      <span class="wordmark__square"></span>
      <span class="wordmark__name">Kestrel Beams</span>
    </div>
    <p class="web-address">www.<strong>kestrelbeams</strong>.com.au</p>
  </section>
</main>
</body>
</html>
```